Wordpress Web Design & Coding for velcorahealth.ca

We need a website for a new investment company that is visually grabbing and vibrant. We would like to see a web page that displays trust, growth and confidence. Needs to be responsive and mobile friendly for all browsers and coded for both Android & IOS.

Open to the number of pages and menu items. I selected 4 but if you feel the layout would work better with less I am open to this. Need to sell the people (management team/related businesses) and then show where the invested money will be going (upcoming projects).

Company Info:

Vel Cora is an investment company put together by a group of seasoned business professionals who have come together to combine decades of success in the real estate development, management, financing and medical services. The company will be a full service company offering turn key solutions for medical professionals.

Vel-Cora will focus on providing a full range of services via a group of distinct companies to deliver newly emerging needs of the medical community. The end goal will be to create complete solutions for individuals in the medical community. Our group has experience and success with the conceptualization, construction and financing of medical and dental clinic spaces. Vel-Cora Solutions will be established to accommodate all areas of the development and creation of clinics for medical professionals from building construction to equipment financing and administrations.

You can mention these companies and take photos from their websites. You can also use stock photos.

Our construction partner:
https://318bld.com/projects/

Our equipment leasing partner:
https://www.norvixa.com/

Our Management Team and medical partners

Gil Parish
https://www.ourfirmstance.ca/

Dietmar Vellasquin
https://www.gshdentalservices.com/about-us

PROPOSED PROJECTS (see attachment for details)
Pinegrove Business Park
Holtmere Business Park
Mt. Corwin Ridge Professional

Target Market(s)

Investors

Industry/Entity Type

Investment

Coding

Coded - Design and coding required

Number of Pages Required

4 page

Font styles to use
Sans Serif

Requirements
Must have
• Wordpress – must be both desktop and mobile friendly with fast page load speed
Ability to edit after ourselves in Wordpress
Attractive home page with logo etc.
Logo colours are: for the blue the pantone color is #0355a3
and for the green is #8cc63f

Sections, about us, what we do/services we provide, contact us

```html
<!DOCTYPE html>
<html lang="en">
<head>
<meta charset="utf-8">
<title>Vel-Cora Solutions</title>
<link rel="stylesheet" href="https://fonts.googleapis.com/css2?family=Montserrat:wght@500;600;700&family=Roboto:wght@400;500&display=swap">
<style>
:root{
  --blue:#0355a3;
  --blue-deep:#0b4595;
  --green:#8cc63f;
  --green-mid:#7ab52f;
  --ink:#1b1b1b;
  --text:#333;
  --muted:#666;
  --light:#f1f1f1;
  --brand-grad:linear-gradient(90deg,#7ab52f 0%,#3f8a55 45%,#0b4a9a 100%);
}
*{box-sizing:border-box;margin:0;padding:0}
html,body{width:1200px;height:4071px;overflow:hidden}
body{position:relative;background:#fff;font-family:'Roboto',Arial,sans-serif;color:var(--text)}
.abs{position:absolute}
.heading{font-family:'Montserrat',Arial,sans-serif;font-weight:700;color:var(--ink)}
.center{text-align:center;left:0;width:1200px}
.btn{display:flex;align-items:center;justify-content:center;color:#fff;font-family:'Roboto',sans-serif;font-weight:500;font-size:14px;background:var(--brand-grad)}
.mark{width:14px;height:14px;background:var(--green);display:block}

/* hero */
.hero{left:0;top:0;width:1200px;height:680px;background:linear-gradient(135deg,#6e6a62 0%,#4a4f56 40%,#2f3540 70%,#3a3b3f 100%)}
.hero::after{content:"";position:absolute;inset:0;background:rgba(0,0,0,.28)}
.brand{left:75px;top:40px;display:flex;align-items:center;gap:10px;z-index:2}
.brand span{font-family:'Montserrat',sans-serif;font-weight:700;font-size:24px;color:var(--blue);letter-spacing:.5px;line-height:1}
.brand i{width:16px;height:16px;background:var(--blue)}
.nav{top:42px;left:452px;display:flex;gap:40px;z-index:2;font-size:16px;color:#fff;text-transform:uppercase}
.nav .on{color:var(--green)}
.nav svg{margin-left:-4px;margin-top:2px}
.hero-text{z-index:2}
.hero-sub{top:347px;font-family:'Montserrat',sans-serif;font-weight:600;font-size:25px;color:#fff;letter-spacing:1px}
.hero-title{top:383px;font-family:'Montserrat',sans-serif;font-weight:700;font-size:52px;color:var(--green)}
.hero-btn{left:516px;top:455px;width:168px;height:45px;z-index:2}
.arrow{z-index:2;top:627px}
.dots{top:638px;left:580px;display:flex;gap:14px;z-index:2}
.dots i{width:14px;height:14px;border-radius:50%;border:2px solid #fff}
.dots i.on{background:#fff}

/* welcome */
.welcome-title{top:778px;font-size:40px}
.welcome-title em{font-style:normal;color:var(--green-mid)}
.welcome-copy{top:848px;left:270px;width:660px;text-align:center;font-size:16px;line-height:22px}
.welcome-btn{left:516px;top:961px;width:168px;height:45px}

/* services */
.services-title{top:1118px;font-size:30px}
.services-copy{top:1178px;left:330px;width:540px;text-align:center;font-size:14px;line-height:22px}
.svc{top:1275px;width:260px}
.svc h3{font-family:'Montserrat',sans-serif;font-weight:600;font-size:18px;color:var(--ink);line-height:22px;height:44px;display:flex;align-items:center}
.svc p{margin-top:18px;font-size:12.5px;line-height:22px;color:#333}
.svc svg{display:block;margin-bottom:18px;height:52px}
.divider{top:1270px;width:1px;height:315px;background:#e6e6e6}

/* what we do */
.what{left:0;top:1712px;width:1200px;height:578px;background:linear-gradient(115deg,#7ab52f 0%,#3f8a55 30%,#0b4a9a 55%)}
.what-photo{left:0;top:1712px;width:1200px;height:578px;background:linear-gradient(160deg,#6a7690 0%,#3c4660 40%,#1d2233 80%,#141722 100%);clip-path:polygon(660px 0,1200px 0,1200px 578px,587px 578px)}
.what-title{left:82px;top:1812px;font-size:38px;color:#fff}
.what-copy{left:82px;top:1880px;width:490px;font-size:14.5px;line-height:22px;color:#fff}
.outline-btn{left:82px;top:2052px;width:180px;height:48px;border:2px solid #fff;color:#fff;font-size:18px;font-weight:500;display:flex;align-items:center;justify-content:center}

/* team */
.team-title{top:2386px;font-size:38px}
.card{top:2495px;width:303px;height:295px;background:#fff;box-shadow:0 3px 14px rgba(0,0,0,.12);text-align:center;padding:30px 26px 0}
.card p{font-size:12.5px;line-height:16px;color:#555}
.card p+p{margin-top:16px}
.card h4{font-family:'Montserrat',sans-serif;font-weight:700;font-size:20px;color:var(--blue);position:absolute;left:0;width:100%;top:187px}
.card.feature{top:2475px;height:315px;background:#1f4f9a;padding-top:34px}
.card.feature p{color:#fff}
.card.feature h4{color:#fff;top:207px}
.avatar{width:98px;height:98px;border-radius:50%;border:4px solid var(--blue);top:2726px}
.avatar.green{border-color:var(--green-mid)}

/* partners */
.partners{left:0;top:2915px;width:1200px;height:457px;background:var(--brand-grad)}
.partners-title{top:2978px;font-size:40px;color:#fff}
.partner{top:3073px;width:230px;height:210px;background:#fff;display:flex;align-items:center;justify-content:center;font-family:'Roboto',sans-serif;font-weight:500;font-size:26px;color:#222}

/* newsletter */
.news{left:0;top:3372px;width:1200px;height:423px;background:var(--light)}
.news-title{top:3442px;font-size:38px}
.news-sub{top:3495px;font-size:17px;color:#333}
.news-rule{left:568px;top:3543px;width:64px;height:3px;background:#222}
.news-form{left:324px;top:3605px;width:552px;height:80px;background:#fff;border:1px solid #ddd}
.news-form span{position:absolute;left:26px;top:27px;font-size:21px;color:#222}
.news-btn{left:371px;top:12px;width:168px;height:55px;font-size:21px;font-weight:400;position:absolute}

/* footer */
.foot{font-size:17px;color:#222;line-height:33px}
.social{display:flex;align-items:center;gap:22px}
.social i{width:14px;height:14px;border-radius:50%;background:#222;display:block}
.foot-brand{left:930px;top:3910px;font-family:'Montserrat',sans-serif;font-weight:700;font-size:30px;color:var(--blue);width:175px;text-align:center;line-height:34px}
.copy{left:840px;top:3992px;font-size:16px;color:#222}
</style>
</head>
<body>

<!-- Hero -->
<div class="abs hero" role="img" aria-label="Photo of a construction manager in a hard hat on the phone at a laptop"></div>
<div class="abs brand"><i></i><span>Vel-Cora Solutions</span></div>
<nav class="abs nav"><span class="on">Home</span><span>About Us</span><span>What We Do</span><span>Services</span><span>Contact Us</span>
<svg width="16" height="16" viewBox="0 0 16 16"><circle cx="6.5" cy="6.5" r="4.5" fill="none" stroke="#fff" stroke-width="2"/><path d="M10 10l4 4" stroke="#fff" stroke-width="2.4" stroke-linecap="round"/></svg></nav>
<div class="abs center hero-text hero-sub">VEL - CORA</div>
<div class="abs center hero-text hero-title">SOLUTIONS</div>
<div class="abs btn hero-btn">LEARN MORE</div>
<svg class="abs arrow" style="left:134px" width="22" height="20" viewBox="0 0 22 20"><path d="M20 10H3M10 3L3 10l7 7" fill="none" stroke="#fff" stroke-width="2.4"/></svg>
<svg class="abs arrow" style="left:1046px" width="22" height="20" viewBox="0 0 22 20"><path d="M2 10h17M12 3l7 7-7 7" fill="none" stroke="#fff" stroke-width="2.4"/></svg>
<div class="abs dots"><i class="on"></i><i></i></div>

<!-- Welcome -->
<i class="abs mark" style="left:593px;top:735px"></i>
<h1 class="abs center heading welcome-title">Welcome To <em>Velcora Solutions</em></h1>
<p class="abs welcome-copy">Vel Cora is an investment company put together by a group of seasoned business professionals who have come together to combine decades of success in the real estate development, management, financing and medical services. The company will be a full service company offering turn key solutions for medical professionals.</p>
<div class="abs btn welcome-btn">READ MORE</div>

<!-- Services -->
<i class="abs mark" style="left:593px;top:1087px"></i>
<h2 class="abs center heading services-title">Our Services</h2>
<p class="abs services-copy">Lorem ipsum dolor sit amet, consectetur adipiscing elit, sed do eiusmod tempor incididunt ut labore et dolore magna aliqua.</p>

<div class="abs svc" style="left:116px">
<svg width="58" height="52" viewBox="0 0 58 52"><defs><linearGradient id="ig" x1="0" x2="1"><stop offset="0" stop-color="#7ab52f"/><stop offset="1" stop-color="#0b4a9a"/></linearGradient></defs><path d="M29 4L3 26h7v22h14V34h10v14h14V26h7z" fill="url(#ig)"/></svg>
<h3>Real estate development</h3>
<p>Lorem ipsum dolor sit amet, consectetur adipiscing elit, sed do eiusmod tempor incididunt ut labore et dolore magna aliqua. Ut enim ad minim veniam, quis nostrud exercitation ullamco laboris.</p></div>
<div class="abs divider" style="left:415px"></div>
<div class="abs svc" style="left:472px">
<svg width="64" height="52" viewBox="0 0 64 52"><circle cx="32" cy="14" r="9" fill="url(#ig)"/><circle cx="12" cy="18" r="6" fill="url(#ig)"/><circle cx="52" cy="18" r="6" fill="url(#ig)"/><path d="M17 46c0-12 7-19 15-19s15 7 15 19z M0 44c0-9 5-14 12-14 3 0 5 1 7 3-3 3-4 7-4 11z M64 44c0-9-5-14-12-14-3 0-5 1-7 3 3 3 4 7 4 11z" fill="url(#ig)"/></svg>
<h3>Management</h3>
<p>Lorem ipsum dolor sit amet, consectetur adipiscing elit, sed do eiusmod tempor incididunt ut labore et dolore magna aliqua. Ut enim ad minim veniam, quis nostrud exercitation ullamco laboris.</p></div>
<div class="abs divider" style="left:777px"></div>
<div class="abs svc" style="left:840px">
<svg width="52" height="52" viewBox="0 0 52 52"><path d="M6 4v14c0 9 6 15 13 15s13-6 13-15V4" fill="none" stroke="url(#ig)" stroke-width="5"/><path d="M19 33v6c0 5 4 9 10 9s10-4 10-9v-9" fill="none" stroke="url(#ig)" stroke-width="5"/><circle cx="39" cy="24" r="6" fill="none" stroke="url(#ig)" stroke-width="4"/></svg>
<h3>Financing and medical services</h3>
<p>Lorem ipsum dolor sit amet, consectetur adipiscing elit, sed do eiusmod tempor incididunt ut labore et dolore magna aliqua. Ut enim ad minim veniam, quis nostrud exercitation ullamco laboris.</p></div>

<!-- What we do -->
<div class="abs what"></div>
<div class="abs what-photo" role="img" aria-label="Photo of an excavator digging on a site at dusk"></div>
<i class="abs mark" style="left:82px;top:1775px"></i>
<h2 class="abs heading what-title">What We do</h2>
<p class="abs what-copy">Sed ut perspiciatis unde omnis iste natus error sit voluptatem accusantium doloremque laudantium, totam rem aperiam, eaque ipsa quae ab illo inventore veritatis et quasi architecto beatae vitae dicta sunt explicabo. Nemo enim ipsam voluptatem quia voluptas sit aspernatur aut odit aut fugit, sed quia consequuntur magni dolores eos qui ratione voluptatem sequi nesciunt. Neque porro quisquam est, qui dolorem</p>
<div class="abs outline-btn">GET IN TOUCH</div>

<!-- Team -->
<h2 class="abs center heading team-title">Team</h2>
<div class="abs card" style="left:117px"><p>A published author and experienced, board-certified physician in the field of Bioidentical Hormone Replacement Therapy.</p><p>Dr. Parish believes in a holistic approach to helping men and women look stunning and feel great.</p><h4>Gil Parish</h4></div>
<div class="abs card feature" style="left:448px" role="img" aria-label="Tinted portrait background"><p>Dietmar brings over 25 years of experience in partnering with dentists across Western Canada as a dental consultant.</p><p>He has been involved in building hundreds of clinics and has assisted clients with clinic location and design, negotiating leases and securing</p><h4>Dietmar</h4></div>
<div class="abs card" style="left:780px"><p>Nor again is there anyone who loves or pursues or desires to obtain pain of itself, because it is pain, but because occasionally circumstances</p><p>Lorem ipsum dolor sit amet, consectetur adipiscing elit, sed do</p><h4>Ned Halvorsen</h4></div>
<div class="abs avatar" style="left:219px;background:#9a6f58" role="img" aria-label="Portrait photo of Gil Parish"></div>
<div class="abs avatar green" style="left:550px;background:#6d6a66" role="img" aria-label="Portrait photo of Dietmar"></div>
<div class="abs avatar" style="left:882px;background:#7d6a5c" role="img" aria-label="Portrait photo of Ned Halvorsen"></div>

<!-- Partners -->
<div class="abs partners"></div>
<h2 class="abs center heading partners-title">Our Partners</h2>
<div class="abs partner" style="left:75px">Arvelo</div>
<div class="abs partner" style="left:348px">Kestra Power</div>
<div class="abs partner" style="left:622px">Bancoria</div>
<div class="abs partner" style="left:896px">Lumen Bay</div>

<!-- Newsletter -->
<div class="abs news"></div>
<h2 class="abs center heading news-title">Subscribe to our newsletter</h2>
<p class="abs center news-sub">Sign up for our email list and get 15% off your first order</p>
<div class="abs news-rule"></div>
<div class="abs news-form"><span>Your email</span><div class="btn news-btn">Subscribe</div></div>

<!-- Footer -->
<div class="abs foot" style="left:82px;top:3865px">Home<br>About<br>What We do</div>
<div class="abs foot" style="left:335px;top:3867px">Services<br>Team<br>Contact Us</div>
<div class="abs foot" style="left:600px;top:3865px">
<div class="social"><i></i>Friendspace</div>
<div class="social"><i></i>Chirper</div>
<div class="social"><i></i>Snapgram</div></div>
<div class="abs foot-brand">Vel-Cora Solutions</div>
<div class="abs copy">© 2020, www.companyname.com</div>

</body>
</html>
```